Wandering Rooms Stationary Set

Wandering Rooms is a bespoke interior design firm set to provide services to VIP clients with elegance and minimalism is the main theme for our stationary set. We require a full stationary set covering A4 letterhead, A4 & A3 envelopes, business cards, USB's, CDs, email signature and any other item the designer sees fit. logo is already designed and finalized, and we require the designer to use it as is without modifying the logo.

Address to be used on letterhead / business cards ...etc shall be as follows:

Phone : +971 2 518 2047
P.O. Box : 309186
Address: Block C&D, Bldg. 47, Court 12, Abu Dhabi, United Arab Emirates
Website: www.wanderingrooms-example.com

Target Market(s)

VIP Clients

Industry/Entity Type

Interior Design

Font styles to use
Other font styles liked:
• something to be unique

Colors

Designer to choose colors to be used in the design.

Requirements
Must have
• Elegant, minimalistic
Nice to have
• Simple yet elegant design having a sharp yet clean cut format
Should not have
• No additional colours, just colours that are used in the logo (silver, black or gold)

```html
<!DOCTYPE html>
<html lang="en">
<head>
<meta charset="utf-8">
<title>Wandering Rooms Stationery Set</title>
<link rel="stylesheet" href="https://fonts.googleapis.com/css2?family=Cormorant+Garamond:wght@500&display=swap">
<style>
  :root {
    --backdrop: #efedea;
    --paper: #ffffff;
    --gold-light: #cbb275;
    --gold-deep: #a8824a;
    --gold-ink: #b08f55;
    --silver-light: #e4e4e4;
    --silver-deep: #b9b9b9;
    --black: #111111;
    --grey-ink: #555555;
  }
  html, body {
    margin: 0;
    width: 1200px;
    height: 893px;
    overflow: hidden;
    background: var(--backdrop);
  }
  .stationery-set { display: block; width: 1200px; height: 893px; }
  .brand-name { font-family: "Cormorant Garamond", serif; font-weight: 500; }
  .detail-text { font-family: "Cormorant Garamond", serif; font-weight: 500; font-size: 7px; fill: var(--grey-ink); }
  .disc-url { font-family: "Cormorant Garamond", serif; font-weight: 500; font-size: 7.5px; letter-spacing: 2px; fill: #ffffff; }
</style>
</head>
<body>
<svg class="stationery-set" viewBox="0 0 1200 893" xmlns="http://www.w3.org/2000/svg">
  <defs>
    <linearGradient id="gold-face" x1="0" y1="0" x2="1" y2="1">
      <stop offset="0" stop-color="var(--gold-light)"/>
      <stop offset="1" stop-color="var(--gold-deep)"/>
    </linearGradient>
    <linearGradient id="gold-flap" x1="0" y1="0" x2="0" y2="1">
      <stop offset="0" stop-color="var(--gold-light)"/>
      <stop offset="1" stop-color="var(--gold-deep)"/>
    </linearGradient>
    <linearGradient id="silver-face" x1="0" y1="0" x2="0" y2="1">
      <stop offset="0" stop-color="var(--silver-light)"/>
      <stop offset="1" stop-color="var(--silver-deep)"/>
    </linearGradient>
  </defs>

  <!-- Envelope, A4 -->
  <g class="envelope envelope-a4">
    <rect x="90" y="80" width="376" height="438" fill="var(--paper)"/>
    <path d="M96 80 H460 L466 130 H90 Z" fill="url(#gold-flap)"/>
    <text class="brand-name" x="116" y="184" font-size="25" fill="var(--gold-ink)">Wandering Rooms</text>
    <line x1="341" y1="149" x2="341" y2="205" stroke="var(--gold-ink)" stroke-width="0.8"/>
    <text class="detail-text" x="354" y="155">P.O. Box : 309186,</text>
    <text class="detail-text" x="354" y="164">Block C&amp;D, Bldg. 47, Court 12</text>
    <text class="detail-text" x="354" y="172">Abu Dhabi, United Arab Emirates</text>
    <circle cx="357" cy="185" r="2" fill="var(--gold-ink)"/>
    <text class="detail-text" x="363" y="187">+971 2 518 2047</text>
    <rect x="355" y="192" width="4.5" height="3" fill="var(--gold-ink)"/>
    <text class="detail-text" x="363" y="196">info@wanderingrooms-example.com</text>
    <circle cx="357" cy="202" r="2" fill="none" stroke="var(--gold-ink)" stroke-width="0.8"/>
    <text class="detail-text" x="363" y="204">www.wanderingrooms-example.com</text>
  </g>

  <!-- CD, lower left -->
  <g class="disc disc-front">
    <circle cx="278" cy="644" r="182" fill="url(#gold-face)" stroke="#ffffff" stroke-width="2"/>
    <circle cx="278" cy="644" r="52" fill="none" stroke="var(--gold-deep)" stroke-width="1.5" opacity="0.6"/>
    <circle cx="278" cy="644" r="24" fill="var(--backdrop)" stroke="#ffffff" stroke-width="2"/>
    <text class="brand-name" x="278" y="552" font-size="26" fill="#ffffff" text-anchor="middle">Wandering Rooms</text>
    <text class="disc-url" x="278" y="739" text-anchor="middle">www.wanderingrooms-example.com</text>
  </g>

  <!-- Envelope, CD sleeve -->
  <g class="envelope envelope-sleeve">
    <rect x="578" y="380" width="374" height="436" fill="var(--paper)"/>
    <path d="M584 380 H946 L952 444 H578 Z" fill="url(#gold-flap)"/>
    <rect x="588" y="446" width="354" height="370" fill="#fafafa"/>
  </g>

  <!-- CD, upper right -->
  <g class="disc disc-sleeved">
    <circle cx="766" cy="258" r="182" fill="url(#gold-face)" stroke="#ffffff" stroke-width="2"/>
    <circle cx="766" cy="258" r="52" fill="none" stroke="var(--gold-deep)" stroke-width="1.5" opacity="0.6"/>
    <circle cx="766" cy="258" r="24" fill="var(--backdrop)" stroke="#ffffff" stroke-width="2"/>
    <text class="brand-name" x="766" y="170" font-size="26" fill="#ffffff" text-anchor="middle">Wandering Rooms</text>
    <text class="disc-url" x="766" y="365" text-anchor="middle">www.wanderingrooms-example.com</text>
  </g>

  <!-- USB drive, gold -->
  <g class="usb usb-gold">
    <path d="M852 526 H1028 V628 H852 Q834 628 834 577 Q834 526 852 526 Z" fill="url(#gold-flap)"/>
    <path d="M912 530 H1100 Q1108 530 1108 540 V614 Q1108 624 1100 624 H912 Q868 624 868 577 Q868 530 912 530 Z" fill="url(#silver-face)"/>
    <circle cx="912" cy="577" r="28" fill="var(--gold-ink)" stroke="#f2f2f2" stroke-width="4"/>
    <text class="brand-name" x="1024" y="582" font-size="14" fill="var(--gold-deep)" text-anchor="middle">Wandering Rooms</text>
  </g>

  <!-- USB drive, black -->
  <g class="usb usb-black">
    <path d="M852 660 H1028 V764 H852 Q834 764 834 712 Q834 660 852 660 Z" fill="var(--black)"/>
    <path d="M912 666 H1100 Q1108 666 1108 676 V748 Q1108 758 1100 758 H912 Q868 758 868 712 Q868 666 912 666 Z" fill="url(#silver-face)"/>
    <circle cx="912" cy="712" r="28" fill="var(--black)" stroke="#f2f2f2" stroke-width="4"/>
    <text class="brand-name" x="1024" y="717" font-size="14" fill="var(--black)" text-anchor="middle">Wandering Rooms</text>
  </g>
</svg>
</body>
</html>
```